Church Website with Home Page and Member Sermon Library

I am in need of an updated design for our church website. This will include 4 pages (outlined below). We are a conservative, evangelical, Christian church. The site should be modern and clean, while still reflecting our conservative values. I already have a logo for our church, and I want the site to incorporate the logo, and match the logo/branding. Stock photos are allowed if needed, but I have uploaded some images of our church and would prefer those images to be used if possible. Any stock photos used should not include any people in the photos (scenery, nature, buildings, animals, etc. are fine).

The site will need 4 pages: Home, Support Us (Donate), Login, and Recording Library.

Page 1: Home
The home page should include the following sections:

- Navigation: Should include links to each section of the home page plus a "listen live" link which will take the user to a live-streaming site and a "support us" link which will take the user to a support/donate page.

- Announcements: Can be either a banner or some other design, but there needs to be some way for us to post announcements for visitors to see. I'm open for creative ideas in this section, but would like it not to take up a lot of room on the page.

- About Us: Should include address, service times (see attached document), and information about the church.

- Pastor Bio: A section that introduces our pastor and gives a short bio about our pastor. Would like this section to include a picture of our pastor. Somewhere in this section I would like to include this Bible reference: "And I will give you pastors according to mine heart, which shall feed you with knowledge and understanding. Jer 3:15 LPW"

- Articles of Faith (What We Believe): This should include several sub-sections each with a heading, body, and possibly 1 or more scripture references. I have attached a document to the brief that includes our articles of faith. Feel free to be creative with this section in how you lay these out and format them.

- Support Us: A small section that explains what kind of support someone can give and a link to a donation page. The link can say something like "Support Us" or "Donate Now".

- Contact form: A contact form that allows the visitor to send us a message. The contact form should ask for name, email, phone, and message.

- Footer: A footer that will be displayed on all pages of the site. This should include at a minimum a link to the home page (or a link to each individual section in the home page if you prefer), a link to "listen live", a link to "support us", a link to "contact us" (or you can put the contact form directly in the footer if you prefer), the address, and a "member login" link.

Page 2: Support Us
The donation page should include a form the visitor can fill out to make a donation. We will embed a third party form later. For this design, please just mock out the design with a basic form asking for name, phone, and email.

Page 3: Login
The recording library (detailed below) will require members to login with a shared numeric code before accessing the page. We need a design for a login screen. The screen should include navigation/footer just like all other pages, but the body of the login page will consist only of a form that asks the user to enter the access code and then a "login" button.

Page 4: Recording Library

The library page is a member-only page that will require a shared, numeric pass code to access. On this page, members will be able to access a filterable list of past sermons. The page by default should display most recent sermons, but should also include a search form that allows the member to filter the sermon list to find a particular sermon. The search form should allow the user to select a filter type (e.g. Speaker name, date, event, etc.) and type in a value to search. They should be able to add multiple filters and remove filters that have been added. Each sermon that is displayed in the result list should include basic information such as title, date, speaker, tags, etc. along with a download icon, and an embedded audio player where they can click a play button to stream it on-demand. Each sermon should also have clickable tags associated with it that can be used to find related sermons.
Updates

I have uploaded several images of our church. Feel free to incorporate these into your design if possible.

Target Market(s)

Church Members

Industry/Entity Type

Religion

Number of Pages Required

4 page

Font styles to use
Sans Serif

Colors

Designer to choose colors to be used in the design.

Requirements
Must have
• Must incorporate the logo (attached)
Nice to have
• Would like the design to incorporate pictures of our church (attached) instead of stock photos if possible.
Should not have
• Please avoid an overly cluttered design. Stock photos used should not include any people in the photos.

```html
<!DOCTYPE html>
<html lang="en">
<head>
<meta charset="utf-8">
<title>Grace Covenant Church</title>
<link rel="stylesheet" href="https://fonts.googleapis.com/css2?family=Cinzel:wght@400;500&family=Montserrat:wght@400;500;600&family=Arimo:ital,wght@0,400;0,700;1,400&display=swap">
<style>
:root{
  --green:#7ba764;
  --cyan:#00bcd9;
  --cyan-light:#2ccbe3;
  --text:#4a4a4a;
  --line:#d9d9d9;
  --paper:#ffffff;
  --sky-top:#5d9bd6;
  --sky-low:#cfe0ef;
  --brick:#8e3b2c;
}
*{box-sizing:border-box;margin:0;padding:0}
html,body{width:1200px;height:4043px;overflow:hidden;background:var(--paper)}
body{position:relative;font-family:"Arimo",Arial,sans-serif;color:var(--text)}

/* header */
.site-header{position:absolute;left:0;top:0;width:1200px;height:83px;background:var(--paper)}
.brand{position:absolute;left:130px;top:18px;display:flex;align-items:center;gap:12px}
.brand-mark{width:16px;height:16px;background:var(--cyan)}
.brand-name{font-family:"Cinzel",serif;font-size:21px;color:var(--cyan);letter-spacing:1px;line-height:48px;white-space:nowrap}
.nav{position:absolute;top:34px;left:390px;display:flex;font-family:"Montserrat",sans-serif;font-size:12.5px;color:#555;letter-spacing:.3px}
.nav a{color:inherit;text-decoration:none}
.nav .sep{color:#aaa;margin:0 36px}
.nav .active{color:var(--cyan)}
.btn{display:flex;align-items:center;justify-content:center;border-radius:24px;color:#fff;font-family:"Montserrat",sans-serif;font-size:14px;letter-spacing:.5px;text-decoration:none}
.btn-green{background:var(--green)}
.btn-cyan{background:var(--cyan)}
.live-btn{position:absolute;left:920px;top:24px;width:157px;height:35px;font-size:12px}

/* hero */
.hero-photo{position:absolute;left:0;top:83px;width:1200px;height:660px;
  background:linear-gradient(180deg,var(--sky-top) 0%,#9cc2e4 38%,var(--sky-low) 56%,#a95a44 64%,var(--brick) 76%,#6f8f3e 86%,#7b9a48 100%)}
.hero-rule{position:absolute;left:0;top:743px;width:1200px;height:3px;background:var(--green)}
.welcome{position:absolute;left:106px;top:299px;width:484px;height:156px;border:1.5px solid var(--green)}
.welcome-tag{position:absolute;left:256px;top:283px;width:196px;height:33px;background:var(--green);color:#fff;font-family:"Cinzel",serif;font-size:21px;letter-spacing:3px;text-align:center;line-height:33px}
.welcome-title{position:absolute;left:106px;top:323px;width:484px;text-align:center;font-family:"Cinzel",serif;font-size:42px;line-height:49px;color:var(--green);white-space:nowrap}
.donate-hero{position:absolute;left:252px;top:435px;width:194px;height:43px;font-size:15px}

/* announcement */
.announce{position:absolute;left:148px;top:815px;width:920px;height:222px;background:var(--green);padding:10px}
.announce-inner{width:100%;height:100%;border:1.5px solid rgba(255,255,255,.8);text-align:center;color:#fff;padding-top:36px}
.announce h2{font-family:"Cinzel",serif;font-weight:400;font-size:33px;letter-spacing:1px}
.announce .rule{width:84px;height:2px;background:#fff;margin:10px auto 20px}
.announce h3{font-weight:700;font-size:15.5px}
.announce p{font-size:13.5px;margin-top:16px}

/* section heads */
.kicker{font-family:"Montserrat",sans-serif;font-size:19px;letter-spacing:3px;color:#555}
.heading{font-family:"Cinzel",serif;font-size:44px;color:var(--green);line-height:1.1}
.rule-green{height:2px;width:90px;background:var(--green)}

/* about */
.about-frame{position:absolute;left:148px;top:1100px;width:372px;height:552px;border:2.5px solid var(--cyan);border-radius:28px;padding:10px}
.about-photo{width:100%;height:100%;border-radius:20px;background:linear-gradient(180deg,#1a6fd0 0%,#5f9fe0 55%,#9a3d2e 62%,#7b3326 100%)}
.about-text{position:absolute;left:600px;top:1155px;width:520px}
.about-text p{font-size:15.5px;line-height:29px;color:#555;margin-bottom:6px}
.timing-title{font-weight:700;color:var(--green);font-size:16.5px;margin-top:20px}
.timings{display:grid;grid-template-columns:275px 240px;row-gap:12px;font-size:14px;margin-top:18px;padding-left:4px;color:#444}

/* pastor */
.pastor{position:absolute;left:0;top:1702px;width:1200px;height:563px;
  background:linear-gradient(180deg,var(--cyan) 0%,var(--cyan-light) 60%,#19c0dc 100%)}
.pastor h2{position:absolute;left:132px;top:120px;font-family:"Cinzel",serif;font-weight:400;font-size:42px;color:#fff}
.pastor .rule-w{position:absolute;left:132px;top:168px;width:92px;height:2px;background:#fff}
.pastor-body{position:absolute;left:132px;top:210px;width:480px;color:#fff;font-size:15.5px;line-height:23px}
.pastor-body p{margin-bottom:8px}
.quote{position:absolute;left:132px;top:358px;width:450px;height:100px;border:1.5px solid rgba(255,255,255,.8);color:#fff;padding:20px 28px;font-size:14px;line-height:20px}
.quote b{display:block;margin-top:10px;font-weight:400}
.pastor-frame{position:absolute;left:667px;top:98px;width:370px;height:375px;border:1.5px solid rgba(255,255,255,.8)}
.pastor-corner{position:absolute;left:922px;top:360px;width:119px;height:116px;background:#fff}
.pastor-photo{position:absolute;left:680px;top:110px;width:348px;height:353px;background:linear-gradient(160deg,#b08a5e 0%,#5a4a3c 45%,#1e1f24 100%)}

/* articles */
.articles-head{position:absolute;left:0;top:2340px;width:1200px;text-align:center}
.articles-head .rule-green{margin:14px auto 0}
.article-outline{position:absolute;left:158px;top:2488px;width:427px;height:490px;border:2px solid var(--green);border-radius:0 110px 0 110px}
.article-photo{position:absolute;left:150px;top:2480px;width:420px;height:486px;border-radius:0 110px 0 110px;background:linear-gradient(180deg,#4a86cf 0%,#a9c9ea 45%,#e9edf0 70%,#6f8b55 100%)}
.faith{position:absolute;left:647px;top:2505px;width:462px}
.faith h3{font-family:"Montserrat",sans-serif;font-weight:500;font-size:21px;letter-spacing:3px;color:#555}
.faith p{font-size:14.5px;line-height:27px;color:#555;margin-top:8px}
.faith .small{font-size:13.5px}
.faith hr{border:0;border-top:1px solid var(--line);margin:26px 0 30px}
.learn-btn{position:absolute;left:647px;top:2917px;width:194px;height:45px;font-size:15px}

/* contact */
.contact{position:absolute;left:0;top:3080px;width:1200px;height:575px;background:linear-gradient(180deg,#f2f4f4 0%,#eef0ef 60%,#dfe3df 78%,#d9d9d4 100%)}
.contact-head{position:absolute;left:0;top:80px;width:1200px;text-align:center}
.field{position:absolute;background:#fff;border:1px solid #cfd3d3;font-size:13.5px;color:#666;padding:0 20px;display:flex;align-items:center}
.field.msg{align-items:flex-start;padding-top:14px}
.send-btn{position:absolute;left:507px;top:442px;width:195px;height:44px;font-size:14px}

/* footer */
.footer{position:absolute;left:0;top:3655px;width:1200px;height:327px;background:#fff}
.footer .brand{left:138px;top:85px}
.vline{position:absolute;top:0;width:1px;height:327px;background:#e3e3e3}
.fcol{position:absolute;top:80px}
.fcol h4{font-family:"Montserrat",sans-serif;font-weight:500;font-size:14.5px;letter-spacing:2px;color:var(--green);border-left:2px solid var(--cyan);padding-left:20px;margin-left:-22px}
.fcol ul{list-style:none;margin-top:18px;font-size:13px;line-height:30px;color:#555;padding-left:4px}
.fcol p{font-size:13px;line-height:19px;color:#555;margin-top:20px}
.small-btn{width:134px;height:30px;font-size:10.5px;margin-top:14px}
.contact-row{display:flex;align-items:flex-start;gap:14px;font-size:12.5px;line-height:17px;color:#444;margin-top:16px}
.icon{flex:0 0 34px;width:34px;height:34px;border-radius:50%;background:var(--green);display:flex;align-items:center;justify-content:center}
.copyright{position:absolute;left:0;top:3982px;width:1200px;height:61px;background:#eef0ef;text-align:center;line-height:61px;font-size:12px;color:#666}
</style>
</head>
<body>

<header class="site-header">
  <div class="brand"><span class="brand-mark"></span><span class="brand-name">Grace Covenant</span></div>
  <nav class="nav">
    <a class="active" href="#home">HOME</a><span class="sep">|</span>
    <a href="#about">ABOUT CHURCH</a><span class="sep">|</span>
    <a href="#library">LIBRARY</a><span class="sep">|</span>
    <a href="#donate">DONATION</a>
  </nav>
  <a class="btn btn-green live-btn" href="#live">LIVE-STREAMING</a>
</header>

<div class="hero-photo" role="img" aria-label="Red brick church with a white steeple under a blue cloudy sky, lawn in front"></div>
<div class="hero-rule"></div>

<div class="welcome"></div>
<div class="welcome-tag">WELCOME TO</div>
<div class="welcome-title">GRACE COVENANT<br>CHURCH</div>
<a class="btn btn-cyan donate-hero" href="#donate">DONATE NOW</a>

<section class="announce">
  <div class="announce-inner">
    <h2>ANNOUNCEMENT</h2>
    <div class="rule"></div>
    <h3>LOREM IPSUM DOLOR SIT AMET, CONSECTETUR ADIPISCING</h3>
    <p>magna aliqua. Ut enim ad minim veniam, quis nostrud exercitation Allamco laboris nisi ut aliquip ex ea</p>
  </div>
</section>

<div class="about-frame"><div class="about-photo" role="img" aria-label="Brick church tower with a white steeple against a blue sky"></div></div>

<section class="about-text" id="about">
  <div class="kicker">GRACE COVENANT</div>
  <div class="heading" style="margin-top:6px">ABOUT OUR CHURCH</div>
  <div class="rule-green" style="margin:12px 0 28px"></div>
  <p>Lorem ipsum dolor sit amet, consectetur adipiscing elit, sed do eiusmod tempor incididunt ut labore et dolore magna aliqua. Ut enim ad minim veniam, quis nostrud exercitation</p>
  <p>Allamco laboris nisi ut aliquip ex ea commodo consequat. Duis aute irure dolor in reprehenderit in voluptate velit esse cillum dolore eu fugiat nulla pariatur. Excepteur sint occaecat cupidatat</p>
  <div class="timing-title">SERVICE TIMING:</div>
  <div class="timings">
    <span>Wednesday Night Service: 7:30 PM</span><span>Sunday Morning Service: 11:00 AM</span>
    <span>Sunday School: 10:00 AM</span><span>Sunday Night Service: 5:30 PM</span>
  </div>
</section>

<section class="pastor">
  <h2>PASTOR BIO</h2>
  <div class="rule-w"></div>
  <div class="pastor-body">
    <p>Lorem ipsum dolor sit amet, consectetur adipiscing elit, sed do eiusmod tempor incididunt ut labore et dolore magna aliqua. Ut enim ad minim veniam, quis nostrud exercitation</p>
    <p>Allamco laboris nisi ut aliquip ex ea commodo consequat. Duis aute irure dolor in reprehenderit in voluptate velit esse</p>
  </div>
  <div class="quote"><em>“And I will give you pastors according to mine heart, which shall feed you with knowledge and understanding”</em><b>Jer 3:15 LPW</b></div>
  <div class="pastor-frame"></div>
  <div class="pastor-corner"></div>
  <div class="pastor-photo" role="img" aria-label="Portrait of the pastor holding an open Bible inside the church"></div>
</section>

<div class="articles-head">
  <div class="kicker">GRACE COVENANT</div>
  <div class="heading" style="margin-top:4px">ARTICLES OF FAITH</div>
  <div class="rule-green"></div>
</div>
<div class="article-outline"></div>
<div class="article-photo" role="img" aria-label="White wooden church with a tall spire against a blue sky"></div>
<section class="faith">
  <h3>THE GOD HEAD.</h3>
  <p>We believe in the God head bodily, known as the Divine Trinity. This body consist of God the father, Jesus Christ, his only begotten son and the redeemer of the world, and of the Holy Ghost, The third person of the Divine Trinity.</p>
  <hr>
  <h3>FULL SALVATION</h3>
  <p class="small">We believe that Salvation is received only when a person comes to the realization that he or she is lost and separated from God and becomes full of godly sorrow, confessing their sins and true repentance, believing in the shed blood of the Lord Jesus Christ as the only sacrifice for sins. Through the blood of Christ we have:</p>
</section>
<a class="btn btn-cyan learn-btn" href="#faith">LEARN MORE</a>

<section class="contact" role="img" aria-label="Faded view of the church building behind the contact form">
  <div class="contact-head">
    <div class="kicker" style="font-size:16px">GET IN TOUCH</div>
    <div class="heading" style="margin-top:2px">CONTACT US</div>
  </div>
  <div class="field" style="left:208px;top:183px;width:390px;height:53px">First Name</div>
  <div class="field" style="left:607px;top:183px;width:391px;height:53px">Last Name</div>
  <div class="field" style="left:208px;top:250px;width:390px;height:53px">Email address</div>
  <div class="field" style="left:607px;top:250px;width:391px;height:53px">Phone</div>
  <div class="field msg" style="left:208px;top:313px;width:790px;height:100px">Message</div>
  <a class="btn btn-cyan send-btn" href="#send">SEND MESSAGE</a>
</section>

<footer class="footer">
  <div class="brand"><span class="brand-mark"></span><span class="brand-name">Grace Covenant</span></div>
  <div class="vline" style="left:397px"></div>
  <div class="vline" style="left:598px"></div>
  <div class="vline" style="left:852px"></div>
  <div class="fcol" style="left:423px">
    <h4>NAVIGATION</h4>
    <ul><li>About Us</li><li>Library</li><li>Donation</li><li>Live Streaming</li><li>Contact Us</li></ul>
  </div>
  <div class="fcol" style="left:620px;width:210px">
    <h4>DONATION</h4>
    <p>Lorem ipsum dolor sit amet, consectetur adipiscing elit, sed do eiusmod tempor inci</p>
    <a class="btn btn-green small-btn" href="#donate">DONATE NOW</a>
  </div>
  <div class="fcol" style="left:874px;width:260px">
    <h4>CONTACT US</h4>
    <div class="contact-row"><span class="icon"><svg width="16" height="18" viewBox="0 0 16 18"><path d="M8 1C4.7 1 2 3.6 2 6.8 2 11 8 17 8 17s6-6 6-10.2C14 3.6 11.3 1 8 1z" fill="#fff"/><circle cx="8" cy="7" r="2.3" fill="#7ba764"/></svg></span><span>88 Cedar Lane, Suite 210, Springfield, ST 00000 USA</span></div>
    <div class="contact-row" style="align-items:center"><span class="icon"><svg width="18" height="14" viewBox="0 0 18 14"><rect x="1" y="1" width="16" height="12" rx="1" fill="none" stroke="#fff" stroke-width="1.6"/><path d="M1.5 2 9 8l7.5-6" fill="none" stroke="#fff" stroke-width="1.6"/></svg></span><span>hello@gracecovenant.org</span></div>
    <div class="contact-row" style="align-items:center"><span class="icon"><svg width="16" height="16" viewBox="0 0 16 16"><path d="M3.5 1.5 6 4.5 4.8 6.3c.9 2 2.5 3.6 4.6 4.7l1.7-1.3 3 2.5-1.4 2.3C7.8 14.3 1.7 8.2 1.3 3z" fill="#fff"/></svg></span><span>(+000) 555 0142</span></div>
  </div>
</footer>
<div class="copyright">© 2023 <u>Grace Covenant Church</u>. All Rights Reserved</div>

</body>
</html>
```